Willow Crest Brand - Bag Design

We are a company dealing with nuts, grains and seeds and are looking for a design for our retail bag packaging that will be consistent across all our product range. We are currently differentiating in way of color but please feel free to be more creative if you wish. Sample of products include pumpkin seeds, rolled oats, almonds, etc.
Design Idea: Hygienic, Natural (from Nature), Quality & Upscale, Simple & Clean design
Target Market: High-end Markets, end-users of A/B type.
1. Bag size is 210 mm (width) * 310 mm (length). Material is OPP or multi-layer PP.
2. Front must have clear window to show packed products. Back clear window is optional.
3. Front side must have logo that stands out (Willow Crest) as attached.
4. Front side must have product name and net weight.
5. Back side must have enough space for Nutrition Fact, product descriptions (110 mm * 100 mm), and barcode.
6. Back side must have white space to print production and expiry dates about 25 mm * 30 mm.
7. Top and bottom of bag must be opaque and not show product.
Reason: Extended period for more new ideas and also for requested modification.
Target Market(s)
Premium market. Type A to B customers as well as professional clients. The product is not a snack. It is for cooking or baking.
Industry/Entity Type
Food Store
Requirements
Must have
- Look unique and stand out from others in the market.
- The colors of the word "Willow Crest" and the blue air-brush in the logo can be changed.
Nice to have
- See project description
Should not have
- See project description

```html
<!DOCTYPE html>
<html lang="en">
<head>
<meta charset="utf-8">
<title>Willow Crest Almonds – Bag Front</title>
<link href="https://fonts.googleapis.com/css2?family=Nunito:wght@700;800&display=swap" rel="stylesheet">
<style>
  :root {
    --backdrop: #d4d4d4;
    --bag-white: #ffffff;
    --brand-red: #b71c2e;
    --brand-navy: #1d1f66;
    --brand-navy-soft: #5e61a8;
    --leaf-green: #1e9a4a;
    --almond-light: #d9a874;
    --almond-dark: #9a6232;
    --net-grey: #9a9a9a;
  }
  html, body {
    margin: 0;
    width: 960px;
    height: 1200px;
    overflow: hidden;
    background: var(--backdrop);
  }
  .bag-front {
    position: absolute;
    left: 100px;
    top: 40px;
    width: 760px;
    height: 1120px;
    display: block;
  }
  .brand-name {
    font-family: "Nunito", sans-serif;
    font-weight: 800;
    font-size: 54px;
    fill: var(--brand-navy);
  }
  .product-name {
    font-family: "Nunito", sans-serif;
    font-weight: 800;
    font-size: 74px;
    fill: var(--bag-white);
  }
  .claim {
    font-family: "Nunito", sans-serif;
    font-weight: 800;
    font-size: 38px;
    fill: var(--bag-white);
  }
  .net-weight {
    font-family: "Nunito", sans-serif;
    font-weight: 700;
    font-size: 19px;
    fill: var(--net-grey);
  }
</style>
</head>
<body>
<svg class="bag-front" viewBox="0 0 768 1135" xmlns="http://www.w3.org/2000/svg">
  <defs>
    <linearGradient id="almond-tone" x1="0" y1="0" x2="1" y2="1">
      <stop offset="0" stop-color="var(--almond-light)"/>
      <stop offset="1" stop-color="var(--almond-dark)"/>
    </linearGradient>
    <linearGradient id="label-band" x1="0" y1="0" x2="1" y2="0">
      <stop offset="0" stop-color="var(--brand-navy)"/>
      <stop offset="1" stop-color="var(--brand-navy-soft)"/>
    </linearGradient>
  </defs>

  <rect class="bag-body" x="0" y="0" width="768" height="1135" fill="var(--bag-white)"/>

  <!-- side bands -->
  <rect class="side-band-left" x="0" y="0" width="84" height="1135" fill="var(--brand-red)"/>
  <rect class="side-band-right" x="686" y="0" width="82" height="1135" fill="var(--brand-red)"/>
  <polygon class="side-band-left-lower" points="0,335 84,362 84,1135 0,1135" fill="var(--brand-navy)"/>
  <polygon class="side-band-right-lower" points="686,640 768,665 768,1135 686,1135" fill="var(--brand-navy)"/>

  <!-- product window -->
  <polygon class="product-window" role="img" aria-label="Photograph of whole natural almonds seen through the clear window"
           points="84,448 686,652 686,1012 84,796" fill="url(#almond-tone)"/>

  <!-- product name band -->
  <polygon class="product-band" points="84,335 540,486 540,598 84,447" fill="url(#label-band)"/>
  <text class="product-name" transform="translate(132,432) rotate(18.3)">Almonds</text>

  <!-- brand name -->
  <circle class="brand-dot" cx="560" cy="235" r="18" fill="var(--brand-navy)"/>
  <text class="brand-name" transform="translate(175,265) rotate(12)">Willow Crest</text>

  <!-- natural claim tag -->
  <polygon class="claim-tag" points="350,912 694,1026 694,1092 344,975" fill="var(--leaf-green)"/>
  <text class="claim" transform="translate(386,968) rotate(18.3)">100% Natural</text>

  <text class="net-weight" x="86" y="1072">Net Wt. 16 OZ (454g)</text>
</svg>
</body>
</html>
```